University Student Business Card

Looking for a professional university student business card. Student is studying business with a focus on marketing. Some combination using a monogram and/or full name on the front with full name, university details and contact information on the back. Card should be modern design for a young professional. Prefer use of royal blue, black and white but am open to other uses of colour palette if it reinforces young/trendy style. Initials for a monogram are: KR. Full details will be provided in private consultation with designer(s).

Target Market(s)

Professional business people, marketers, advertisers, consultants

Industry/Entity Type

Business, marketing

Contact Information for Business Card

Monogram or personal logo, full name, university name, program of study, phone number, email address, pathfolio address

Other font styles liked:
• Open to suggestion to fulfill above requirements

Colors
0054AA
0677BA
7BADD7
CADEEF
E8F1F8

Requirements
Must have
• Monogram using letters K and R, and incorporate the business card details listed in the brief (specific details including personal contact info will be shared with successful designer to ensure privacy)
Nice to have
• Personal brand using monogram or personal logo (not a business logo)

```html
<!DOCTYPE html>
<html lang="en">
<head>
<meta charset="utf-8">
<title>Kieran Rhodes – Student Business Card</title>
<link rel="stylesheet" href="https://fonts.googleapis.com/css2?family=Bebas+Neue&family=Arimo:wght@400&display=swap">
<style>
  :root {
    --stage: #2a2a2c;
    --card: #1c1d1f;
    --card-texture: #202123;
    --royal: #0054aa;
    --sky: #0677ba;
    --grey-text: #a3a5a8;
    --rule: #8d8f92;
    --white: #ffffff;
  }
  * { box-sizing: border-box; margin: 0; padding: 0; }
  html, body { width: 1200px; height: 1108px; overflow: hidden; }
  body {
    background: var(--stage);
    display: flex; align-items: center; justify-content: center; gap: 80px;
    font-family: "Arimo", Arial, sans-serif;
  }
  .card {
    position: relative;
    width: 420px; height: 680px;
    background: var(--card);
    border-radius: 22px;
    overflow: hidden;
    display: flex; flex-direction: column; align-items: center;
    text-align: center;
  }
  /* Back */
  .card--back { justify-content: center; padding-bottom: 40px; }
  .university {
    font-family: "Bebas Neue", "Arial Narrow", sans-serif;
    color: var(--royal);
    font-size: 92px; line-height: 0.9;
  }
  .rule { width: 190px; height: 1px; background: var(--rule); margin: 26px 0 18px; }
  .address { color: var(--grey-text); font-size: 19px; line-height: 1.3; }
  .icon-row { display: flex; align-items: center; gap: 8px; margin: 26px 0 20px; }
  .icon-row .line { width: 52px; height: 1px; background: var(--rule); }
  .icon {
    width: 32px; height: 32px; background: var(--royal); border-radius: 4px;
    display: flex; align-items: center; justify-content: center;
  }
  .contact { color: var(--grey-text); font-size: 19px; line-height: 1.35; }
  /* Front */
  .card--front { justify-content: center; }
  .texture {
    position: absolute; inset: 0;
    background: var(--card-texture);
  }
  .front-content { position: relative; display: flex; flex-direction: column; align-items: center; margin-top: 30px; }
  .monogram {
    font-family: "Bebas Neue", "Arial Narrow", sans-serif;
    color: var(--royal);
    font-size: 230px; line-height: 0.85; letter-spacing: 4px;
  }
  .person {
    font-family: "Bebas Neue", "Arial Narrow", sans-serif;
    color: var(--royal);
    font-size: 52px; line-height: 1; margin-top: 50px;
  }
  .role { color: var(--white); font-size: 20px; margin-top: 4px; }
  .front-rule { width: 90px; height: 1px; background: var(--white); margin: 16px 0 14px; }
  .profile { display: flex; align-items: center; gap: 10px; color: var(--white); font-size: 20px; }
  .profile .dot { width: 26px; height: 26px; border-radius: 50%; background: var(--sky); }
</style>
</head>
<body>
  <section class="card card--back">
    <h1 class="university">University<br>Name</h1>
    <div class="rule"></div>
    <p class="address">421, Address line here<br>45452, Country Name</p>
    <div class="icon-row">
      <span class="line"></span>
      <span class="icon" aria-label="Phone">
        <svg width="20" height="20" viewBox="0 0 24 24"><path fill="#1c1d1f" d="M6.6 10.8a15 15 0 0 0 6.6 6.6l2.2-2.2c.3-.3.7-.4 1-.2 1.1.4 2.3.6 3.6.6.6 0 1 .4 1 1V20c0 .6-.4 1-1 1A17 17 0 0 1 3 4c0-.6.4-1 1-1h3.5c.6 0 1 .4 1 1 0 1.3.2 2.5.6 3.6.1.3 0 .7-.2 1z"/></svg>
      </span>
      <span class="icon" aria-label="Email">
        <svg width="20" height="20" viewBox="0 0 24 24"><rect x="3" y="6" width="18" height="12" fill="none" stroke="#1c1d1f" stroke-width="2"/><path d="M3 6l9 7 9-7" fill="none" stroke="#1c1d1f" stroke-width="2"/></svg>
      </span>
      <span class="icon" aria-label="Website">
        <svg width="20" height="20" viewBox="0 0 24 24"><circle cx="12" cy="12" r="8.5" fill="none" stroke="#1c1d1f" stroke-width="2"/><path d="M3.5 12h17M12 3.5c3 3 3 14 0 17M12 3.5c-3 3-3 14 0 17" fill="none" stroke="#1c1d1f" stroke-width="1.6"/></svg>
      </span>
      <span class="line"></span>
    </div>
    <p class="contact">044-555 018 273<br>hello@kieranrhodes.com<br>www.kieranrhodes.com</p>
  </section>

  <section class="card card--front">
    <div class="texture" role="img" aria-label="Faint repeating monogram pattern across the card"></div>
    <div class="front-content">
      <div class="monogram">KR</div>
      <h2 class="person">Kieran Rhodes</h2>
      <p class="role">Business Marketing</p>
      <div class="front-rule"></div>
      <p class="profile"><span class="dot"></span>pathfolio.com/name</p>
    </div>
  </section>
</body>
</html>
```